Business Card Design

We like to use greens as you will see in our logo (but not TOO much green). We are a Dental Clinic in a somewhat eccentric community. We do not like the dated sharp designs which we see many dentists use. We're looking for something bright and fresh while still maintaining the integrity of the profession. Elegance is not necessarily what we are going for... we need for the design to be "mature" but also up-lifting.

See our logo.
Updates

Project Deadline Extended
Reason: We have 5 designs which we like. But we'd like to see a few more before committing to a design.

Project Deadline Extended
Reason: We are awaiting revisions to this project. We are still welcoming designs while we wait to see if designers are able to provide to us the revisions we require in order to proceed with a selection.

Target Market(s)

Younger families - ages late 20's to early 40's

Industry/Entity Type

Business

Contact Information for Business Card

Corwel T. Banfry DDS 2730 W. Halvert Rd. Ste. 7 Royal Oak, MI 48391 (248)555-0174 FX (248)555-0189 info@BrightwellDentalCareMi.com BrigthwellDentalCareMi.com on the back of the card we need an appointment reminder (For____ Date___ Time____) with "If you are unable to keep your appointment, kindly give 48 hours notice" at the bottom. No use of teeth in the design. DOUBLE SIDED DESIGN

Requirements
Should not have
• The use of pictures of teeth

```html
<!DOCTYPE html>
<html lang="en">
<head>
<meta charset="utf-8">
<title>Brightwell Dental Care – Business Card</title>
<link rel="stylesheet" href="https://fonts.googleapis.com/css2?family=Source+Sans+3:ital,wght@0,400;0,600;0,700;1,400&family=Marcellus+SC&display=swap">
<style>
  :root {
    --green-dark: #1f6b35;
    --green-mid: #2e8b3e;
    --green-light: #3aa33c;
    --green-pale: #8fcf5a;
    --ink: #2b2b2b;
    --rule: #c9c9c9;
    --card: #ffffff;
    --backdrop: #eeeeea;
    --card-edge: #9a9a9a;
  }
  * { box-sizing: border-box; margin: 0; padding: 0; }
  html, body { width: 1200px; height: 1178px; overflow: hidden; }
  body {
    background: var(--backdrop);
    font-family: "Source Sans 3", "Segoe UI", sans-serif;
    color: var(--ink);
    position: relative;
  }
  .card {
    position: absolute;
    width: 916px;
    height: 526px;
    background: var(--card);
    border: 2px solid var(--card-edge);
    border-radius: 32px;
    overflow: hidden;
  }
  .card--front { left: 262px; top: 33px; }
  .card--back  { left: 30px;  top: 606px; }

  /* Wordmark */
  .wordmark { position: absolute; display: flex; align-items: center; gap: 14px; color: var(--green-dark); font-weight: 600; }
  .wordmark__dot { border-radius: 50%; background: var(--green-pale); flex: none; }
  .wordmark__text { display: flex; flex-direction: column; align-items: center; line-height: 1; }
  .wordmark__name { letter-spacing: 0.5px; }
  .wordmark__sub { letter-spacing: 1px; text-transform: uppercase; }

  .card--front .wordmark { left: 0; right: 0; top: 92px; justify-content: center; }
  .card--front .wordmark__dot { width: 44px; height: 44px; }
  .card--front .wordmark__name { font-size: 84px; }
  .card--front .wordmark__sub { font-size: 44px; margin-top: 8px; }

  .card--back .wordmark { right: 50px; top: 50px; gap: 10px; }
  .card--back .wordmark__dot { width: 26px; height: 26px; }
  .card--back .wordmark__name { font-size: 50px; }
  .card--back .wordmark__sub { font-size: 26px; margin-top: 4px; }

  /* Front details */
  .doctor { position: absolute; left: 0; right: 0; top: 296px; text-align: center; font-size: 29px; font-weight: 700; color: var(--green-dark); }
  .doctor__degree { font-weight: 400; color: var(--ink); font-size: 26px; }
  .doctor-rule { position: absolute; left: 56px; right: 80px; top: 354px; height: 3px; border-radius: 2px; background: linear-gradient(90deg, transparent, var(--rule) 15%, var(--rule) 85%, transparent); }
  .contact-line { position: absolute; left: 0; right: 0; text-align: center; font-size: 23px; display: flex; justify-content: center; align-items: center; gap: 8px; }
  .contact-line--phones { top: 380px; }
  .contact-line--web { top: 420px; }
  .contact-line--address { top: 472px; }
  .contact-line svg { width: 20px; height: 20px; flex: none; }
  .contact-line .gap { width: 10px; }

  /* Back */
  .appt-title { position: absolute; left: 73px; top: 100px; font-family: "Marcellus SC", Georgia, serif; font-size: 33px; color: var(--green-dark); letter-spacing: 1px; }
  .field { position: absolute; font-size: 25px; }
  .dots { position: absolute; border-bottom: 2px dotted #555; height: 0; }
  .slot { position: absolute; top: 306px; height: 37px; width: 164px; border: 2px solid #555; border-radius: 5px; }
  .day-band { position: absolute; left: 0; right: 0; top: 362px; height: 76px; display: flex; }
  .day-band__week { width: 725px; background: var(--green-dark); }
  .day-band__sat { flex: 1; background: var(--green-light); border-left: 4px solid #fff; }
  .day { position: absolute; top: 386px; color: #fff; font-weight: 700; font-size: 27px; line-height: 30px; }
  .day-box { position: absolute; top: 384px; width: 56px; height: 33px; background: #fff; border-radius: 4px; border: 1px solid #888; }
  .notice { position: absolute; left: 0; right: 0; top: 462px; text-align: center; font-style: italic; font-size: 25px; }
</style>
</head>
<body>

<section class="card card--front" aria-label="Business card front">
  <div class="wordmark">
    <span class="wordmark__dot"></span>
    <div class="wordmark__text">
      <span class="wordmark__name">Brightwell</span>
      <span class="wordmark__sub">Dental Care</span>
    </div>
  </div>

  <p class="doctor">Corwel T. Banfry, <span class="doctor__degree">DDS</span></p>
  <div class="doctor-rule"></div>

  <p class="contact-line contact-line--phones">
    <svg viewBox="0 0 20 20" aria-hidden="true"><path d="M5 2l3 4-2 2c1 2 3 4 5 5l2-2 4 3-2 3C9 17 3 11 2 5z" fill="none" stroke="#222" stroke-width="1.6"/></svg>
    <span>(248)555-0174</span><span class="gap"></span>
    <svg viewBox="0 0 20 20" aria-hidden="true"><rect x="5" y="3" width="10" height="5" fill="#222"/><rect x="2" y="8" width="16" height="7" rx="1.5" fill="#222"/><rect x="5" y="13" width="10" height="4" fill="#222"/></svg>
    <span>(248)555-0189</span>
  </p>
  <p class="contact-line contact-line--web">
    <svg viewBox="0 0 20 20" aria-hidden="true"><rect x="2" y="5" width="16" height="11" rx="1" fill="#222"/><path d="M2.5 6l7.5 5 7.5-5" fill="none" stroke="#fff" stroke-width="1.4"/></svg>
    <span>info@BrightwellDentalCareMi.com</span><span class="gap"></span>
    <svg viewBox="0 0 20 20" aria-hidden="true"><g fill="none" stroke="#222" stroke-width="1.5"><circle cx="10" cy="10" r="7.5"/><ellipse cx="10" cy="10" rx="3.5" ry="7.5"/><path d="M2.5 10h15M4 6h12M4 14h12"/></g></svg>
    <span>BrigthwellDentalCareMi.com</span>
  </p>
  <p class="contact-line contact-line--address">2730 W. Halvert Rd. Ste. 7 Royal Oak, MI 48391</p>
</section>

<section class="card card--back" aria-label="Appointment card back">
  <h2 class="appt-title">YOUR APPOINTMENT</h2>
  <div class="wordmark">
    <span class="wordmark__dot"></span>
    <div class="wordmark__text">
      <span class="wordmark__name">Brightwell</span>
      <span class="wordmark__sub">Dental Care</span>
    </div>
  </div>

  <span class="field" style="left:82px; top:177px;">Name :</span>
  <span class="dots" style="left:184px; width:665px; top:200px;"></span>

  <span class="field" style="left:82px; top:242px;">Date :</span>
  <span class="dots" style="left:184px; width:227px; top:265px;"></span>
  <span class="field" style="left:421px; top:242px;">Time :</span>
  <span class="dots" style="left:502px; width:240px; top:265px;"></span>
  <span class="field" style="left:753px; top:242px;">am / pm</span>

  <span class="field" style="left:82px; top:307px;">Next Appointment</span>
  <span class="slot" style="left:331px;"></span>
  <span class="slot" style="left:508px;"></span>
  <span class="slot" style="left:684px;"></span>

  <div class="day-band"><div class="day-band__week"></div><div class="day-band__sat"></div></div>
  <span class="day" style="left:81px;">MON</span><span class="day-box" style="left:159px;"></span>
  <span class="day" style="left:229px;">TUE</span><span class="day-box" style="left:292px;"></span>
  <span class="day" style="left:362px;">WED</span><span class="day-box" style="left:436px;"></span>
  <span class="day" style="left:505px;">THU</span><span class="day-box" style="left:573px;"></span>
  <span class="day" style="left:641px;">FRI</span><span class="day-box" style="left:694px;"></span>
  <span class="day" style="left:764px;">SAT</span><span class="day-box" style="left:824px;"></span>

  <p class="notice">If you are unable to keep your appointment, kindly give 48 hours notice</p>
</section>

</body>
</html>
```